Business card for law firm

Need business card for new law firm. Think confident, authoritative, conservative, but not stuffy or old-fashioned.

Contact Information for Business Card

Content for card - logo (uploaded), plus the following:

Paul Whitcombe (larger font)
Managing Partner (larger font, but not as large as name)
Level 9, 7 Ferris Lane
Sydney NSW 2000
Main Tel 02 9364 2710
Direct Tel 02 8472 3159
Email paul@qvlegal.com.au
www.qvlegal.com.au

Letterhead design should include logo plus:
Level 9, 7 Ferris Lane
Sydney NSW 2000
Tel 02 8472 3159
www.qvlegal.com.au

```html
<!DOCTYPE html>
<html lang="en">
<head>
<meta charset="utf-8">
<title>Quayvale Legal – Business Card</title>
<link rel="stylesheet" href="https://fonts.googleapis.com/css2?family=Cinzel:wght@400&family=Open+Sans:wght@400&display=swap">
<style>
  :root {
    --stage: #1c1c1e;
    --card: #111112;
    --card-edge: #2a2a2c;
    --ink: #f2f2f2;
    --ink-soft: #c9c9cc;
    --rule: #3a3a3d;
    --icon: #e6e6e6;
  }
  * { margin: 0; padding: 0; box-sizing: border-box; }
  html, body {
    width: 1200px; height: 900px; overflow: hidden;
    background: var(--stage);
  }
  .stage {
    position: relative; width: 1200px; height: 900px;
    display: flex; flex-direction: column; align-items: center; justify-content: center; gap: 40px;
  }
  .card {
    position: relative; width: 640px; height: 390px;
    background: var(--card);
    border: 1px solid var(--card-edge);
    border-radius: 22px;
  }
  /* back side */
  .card--back { display: flex; align-items: center; justify-content: center; }
  .back-mark {
    display: flex; align-items: center; gap: 16px;
    font-family: "Cinzel", serif; font-size: 40px; color: var(--ink-soft); letter-spacing: 3px;
  }
  .back-mark .square { width: 22px; height: 22px; background: var(--ink-soft); }
  /* front side */
  .firm {
    position: absolute; top: 64px; right: 44px;
    display: flex; align-items: center; gap: 14px;
    font-family: "Cinzel", serif; font-size: 34px; color: var(--ink); letter-spacing: 2px;
  }
  .firm .square { width: 16px; height: 16px; background: var(--ink); }
  .rule-top {
    position: absolute; top: 132px; right: 44px; width: 300px; height: 1px; background: var(--rule);
  }
  .person { position: absolute; left: 44px; bottom: 40px; }
  .person-name {
    font-family: "Cinzel", serif; font-size: 24px; color: var(--ink); letter-spacing: 1px;
    padding-bottom: 4px; border-bottom: 1px solid var(--rule); width: 330px;
  }
  .person-role {
    font-family: "Open Sans", sans-serif; font-size: 17px; color: var(--ink-soft); margin: 6px 0 10px;
  }
  .contacts { list-style: none; font-family: "Open Sans", sans-serif; font-size: 16px; color: var(--ink-soft); }
  .contacts li { display: flex; align-items: center; gap: 10px; line-height: 25px; }
  .contacts svg { width: 14px; height: 14px; flex: none; fill: var(--icon); }
  .contacts .note { font-size: 13px; letter-spacing: 0.5px; }
  .address {
    position: absolute; right: 44px; bottom: 132px; text-align: right;
    font-family: "Open Sans", sans-serif; font-size: 16px; line-height: 22px; color: var(--ink-soft);
  }
</style>
</head>
<body>
<main class="stage">
  <section class="card card--back" aria-label="Card back">
    <div class="back-mark"><span class="square"></span>QUAYVALE LEGAL</div>
  </section>

  <section class="card card--front" aria-label="Card front">
    <div class="firm"><span class="square"></span>QUAYVALE LEGAL</div>
    <div class="rule-top"></div>

    <div class="address">
      <p>Level 9, 7 Ferris Lane</p>
      <p>Sydney NSW 2000</p>
    </div>

    <div class="person">
      <h1 class="person-name">PAUL WHITCOMBE</h1>
      <p class="person-role">Managing Partner</p>
      <ul class="contacts">
        <li>
          <svg viewBox="0 0 16 16" aria-hidden="true"><path d="M1 5c0-2 3-3 7-3s7 1 7 3v1h-3V5H4v1H1z"/><path d="M3 7h10l1 7H2z"/></svg>
          02 9364 2710
        </li>
        <li>
          <svg viewBox="0 0 16 16" aria-hidden="true"><path d="M1 5c0-2 3-3 7-3s7 1 7 3v1h-3V5H4v1H1z"/><path d="M3 7h10l1 7H2z"/></svg>
          02 8472 3159 <span class="note">(DIRECT)</span>
        </li>
        <li>
          <svg viewBox="0 0 16 16" aria-hidden="true"><path d="M1 3h14v10H1z M2 4l6 5 6-5" fill="none" stroke="#e6e6e6" stroke-width="1.6"/></svg>
          paul@qvlegal.com.au
        </li>
        <li>
          <svg viewBox="0 0 16 16" aria-hidden="true"><circle cx="8" cy="8" r="6.5" fill="none" stroke="#e6e6e6" stroke-width="1.5"/><path d="M1.5 8h13M8 1.5c-3 3-3 10 0 13M8 1.5c3 3 3 10 0 13" fill="none" stroke="#e6e6e6" stroke-width="1.2"/></svg>
          www.qvlegal.com.au
        </li>
      </ul>
    </div>
  </section>
</main>
</body>
</html>
```